Plakat-Design 24h Betreuung
Zielgruppe
Wir vermitteln 24h Pflege- und Betreuungskräfte für alte und hilfbedürftige Menschen!
Zielgruppe: deren Angehörige (zwischen 50-70 Jahre alt)
Aufgabenstellung
Klare Ansage - nicht zu verspielt - geradlinig
Maße Plakat: 504 cm breit x 238 cm hoch
Das PLAKAT ist ca 10 m von der Straße entfernet und ist für Autofahrer gedacht - somit muss man alles gut lesen können und groß geschrieben sein !!!!
Folgender Text und Bilder sollte das Plakat beinhalten:
24h - Betreuung (groß links oben platziert)
Logo: SorgeFreund.at
Foto mit 10 Personen
Erfahrung seit 2010
www.sorgefreund.at

```html
<!DOCTYPE html>
<html lang="de">
<head>
<meta charset="utf-8">
<title>24h - Betreuung Plakat</title>
<link rel="stylesheet" href="https://fonts.googleapis.com/css2?family=Montserrat:wght@500;600;700;800&display=swap">
<style>
  :root {
    --stage: #22252f;
    --paper: #ffffff;
    --navy: #2b4180;
    --orange: #d4691e;
    --photo-light: #eef0f4;
    --photo-dark: #3a4670;
  }
  * { margin: 0; padding: 0; box-sizing: border-box; }
  html, body {
    width: 1036px; height: 1200px; overflow: hidden;
    background: var(--stage);
    font-family: "Montserrat", Arial, sans-serif;
  }
  .poster {
    position: absolute; left: 61px;
    width: 914px; height: 485px;
    background: var(--paper);
  }
  .poster--orange { top: 61px; --badge: var(--orange); }
  .poster--navy { top: 653px; --badge: var(--navy); }

  .headline {
    position: absolute; left: 47px; top: 42px;
    font-size: 68px; font-weight: 800; letter-spacing: -0.5px;
    color: var(--navy); line-height: 1; white-space: nowrap;
  }
  .badge {
    position: absolute; left: 708px; top: 16px;
    width: 186px; height: 186px; border-radius: 50%;
    background: var(--badge);
    display: flex; flex-direction: column; align-items: center; justify-content: center;
    color: var(--paper); text-align: center;
  }
  .badge::after {
    content: ""; position: absolute; inset: 8px;
    border: 2.5px solid var(--paper); border-radius: 50%;
  }
  .badge__label { font-size: 21px; font-weight: 500; line-height: 1.0; }
  .badge__year { font-size: 44px; font-weight: 700; line-height: 1.1; margin-top: 2px; }

  .brand {
    position: absolute; left: 58px; top: 182px;
    display: flex; align-items: center; gap: 8px;
    font-size: 21px; font-weight: 600; color: var(--navy);
  }
  .brand__dot { width: 12px; height: 12px; border-radius: 50%; background: var(--orange); }

  .team-photo {
    position: absolute; left: 296px; top: 150px;
    width: 330px; height: 243px;
    background: linear-gradient(180deg, var(--photo-light) 0%, var(--photo-dark) 100%);
    border-radius: 4px;
  }

  .locations {
    position: absolute; left: 36px; top: 401px;
    font-size: 22px; font-weight: 500; color: var(--navy); line-height: 31px;
  }
  .locations dt { display: inline; color: var(--orange); font-weight: 700; }
  .locations dd { display: inline; }
  .locations div { white-space: nowrap; }

  .web {
    position: absolute; left: 577px; top: 408px;
    width: 315px; height: 45px;
    background: var(--navy); color: var(--paper);
    display: flex; align-items: center; justify-content: center;
    font-size: 22px; font-weight: 700;
  }
</style>
</head>
<body>
  <section class="poster poster--orange">
    <h1 class="headline">24h - Betreuung</h1>
    <div class="badge"><span class="badge__label">Erfahrung<br>seit</span><span class="badge__year">2010</span></div>
    <div class="brand"><span>SorgeFreund.at</span><span class="brand__dot"></span></div>
    <div class="team-photo" role="img" aria-label="Gruppenfoto des Teams mit zehn Personen in weißen Blusen und dunkler Kleidung"></div>
    <dl class="locations">
      <div><dt>Zentrale:</dt> <dd>Bergfeld am See</dd></div>
      <div><dt>Zweigstelle:</dt> <dd>Lindenkirchen</dd></div>
    </dl>
    <div class="web">www.sorgefreund.at</div>
  </section>

  <section class="poster poster--navy">
    <h1 class="headline">24h - Betreuung</h1>
    <div class="badge"><span class="badge__label">Erfahrung<br>seit</span><span class="badge__year">2010</span></div>
    <div class="brand"><span>SorgeFreund.at</span><span class="brand__dot"></span></div>
    <div class="team-photo" role="img" aria-label="Gruppenfoto des Teams mit zehn Personen in weißen Blusen und dunkler Kleidung"></div>
    <dl class="locations">
      <div><dt>Zentrale:</dt> <dd>Bergfeld am See</dd></div>
      <div><dt>Zweigstelle:</dt> <dd>Lindenkirchen</dd></div>
    </dl>
    <div class="web">www.sorgefreund.at</div>
  </section>
</body>
</html>
```